Velmora Freightway Solutions Business cards

Would like a very unique design catchy but professional for business cards. Please use log provided.Marlon WellsCeo and Founder TransCon Logistix Solutions1-888-913-3225mwells@tlsolutionsus.comwww.tlsolutionsus.com

```html
<!DOCTYPE html>
<html lang="en">
<head>
<meta charset="utf-8">
<title>Velmora Freightway Solutions – Business Cards</title>
<link href="https://fonts.googleapis.com/css2?family=Lato:wght@400;700&display=swap" rel="stylesheet">
<style>
  :root {
    --brand-blue: #1170bb;
    --brand-red: #ec1c2b;
    --ink-black: #000000;
    --paper: #ffffff;
    --stage: #e9e7e4;
    --muted: #333333;
  }
  * { margin: 0; padding: 0; box-sizing: border-box; }
  html, body {
    width: 1200px; height: 960px; overflow: hidden;
    background: var(--stage);
    font-family: "Lato", Arial, sans-serif;
  }
  .card {
    position: absolute;
    border-radius: 26px;
    overflow: hidden;
    background: var(--paper);
    box-shadow: 0 6px 16px rgba(0,0,0,0.18);
  }
  /* Front */
  .card-front { left: 238px; top: 48px; width: 720px; height: 404px; }
  .front-name {
    position: absolute; left: 0; right: 0; top: 120px;
    text-align: center;
    color: var(--brand-blue);
    font-weight: 700;
    font-size: 62px;
    line-height: 1.1;
    letter-spacing: 1px;
    text-transform: uppercase;
  }
  .front-web {
    position: absolute; left: 0; right: 0; top: 358px;
    display: flex; align-items: center; justify-content: center; gap: 12px;
    font-size: 15px; letter-spacing: 2.5px; color: var(--muted);
  }
  .front-web .rule { height: 2px; width: 90px; background: var(--brand-blue); border-radius: 2px; }
  /* Back */
  .card-back { left: 244px; top: 507px; width: 706px; height: 407px; background: var(--ink-black); border-radius: 18px; }
  .back-art { position: absolute; left: 0; top: 0; }
  .back-name {
    position: absolute; left: 220px; top: 30px; width: 460px;
    text-align: right; color: var(--paper);
  }
  .back-name .person { font-size: 22px; font-weight: 700; letter-spacing: 0.3px; }
  .back-name .role { font-size: 17px; margin-top: 6px; letter-spacing: 0.3px; }
  .back-brand {
    position: absolute; left: 30px; top: 76px; width: 350px;
    text-align: center; color: var(--brand-blue);
    font-size: 24px; font-weight: 700; letter-spacing: 1.5px;
    text-transform: uppercase; line-height: 1.25;
  }
  .back-brand .brand-square {
    display: block; width: 34px; height: 34px; margin: 0 auto 12px;
    background: var(--brand-red);
  }
  .contact-list {
    position: absolute; right: 28px; top: 298px;
    list-style: none; color: var(--paper); font-size: 17px;
  }
  .contact-list li {
    display: flex; align-items: center; justify-content: flex-end;
    gap: 8px; height: 30px; white-space: nowrap;
  }
  .address {
    position: absolute; left: 26px; top: 332px;
    color: var(--paper); font-size: 17px; line-height: 27px;
    display: flex; align-items: flex-start; gap: 5px;
  }
  .address .icon { margin-top: 5px; }
  .icon { display: block; width: 16px; height: 16px; flex: none; }
</style>
</head>
<body>

<section class="card card-front">
  <div class="front-name">Velmora<br>Freightway Solutions</div>
  <div class="front-web"><span class="rule"></span><span>www.vfwayroutes.com</span><span class="rule"></span></div>
</section>

<section class="card card-back">
  <svg class="back-art" width="706" height="407" viewBox="0 0 706 407">
    <ellipse cx="150" cy="40" rx="282" ry="244" fill="none" stroke="var(--brand-blue)" stroke-width="2"/>
    <ellipse cx="150" cy="40" rx="277" ry="239" fill="none" stroke="var(--brand-red)" stroke-width="5"/>
    <ellipse cx="150" cy="40" rx="272" ry="234" fill="var(--paper)"/>
    <ellipse cx="150" cy="40" rx="268" ry="230" fill="none" stroke="var(--brand-blue)" stroke-width="1.2"/>
    <path d="M0,188 C120,270 280,292 420,252 C540,218 640,204 706,208 L706,407 L0,407 Z" fill="var(--paper)"/>
    <path d="M0,194 C120,276 280,298 420,258 C540,224 640,210 706,214 L706,407 L0,407 Z" fill="var(--ink-black)"/>
    <path d="M0,208 C120,288 280,304 420,266 C540,232 640,218 706,222 L706,407 L0,407 Z" fill="var(--brand-red)"/>
    <path d="M0,218 C120,296 280,312 420,274 C540,240 640,228 706,232 L706,407 L0,407 Z" fill="var(--paper)"/>
    <path d="M0,222 C120,300 280,316 420,278 C540,244 640,232 706,236 L706,407 L0,407 Z" fill="var(--brand-blue)"/>
  </svg>

  <div class="back-brand"><span class="brand-square"></span>Velmora Freightway<br>Solutions</div>

  <div class="back-name">
    <div class="person">DORIAN PIKE</div>
    <div class="role">CEO AND FOUNDER</div>
  </div>

  <div class="address">
    <svg class="icon" viewBox="0 0 16 16"><path d="M8 1a5 5 0 0 0-5 5c0 4 5 9 5 9s5-5 5-9a5 5 0 0 0-5-5z" fill="none" stroke="#fff" stroke-width="1.5"/><circle cx="8" cy="6" r="1.8" fill="#fff"/></svg>
    <div>2417 Cedar Vale Rd<br>Atlanta, GA 30327</div>
  </div>

  <ul class="contact-list">
    <li><span>1-888-470-6158</span>
      <svg class="icon" viewBox="0 0 16 16"><circle cx="8" cy="8" r="7" fill="none" stroke="#fff" stroke-width="1.3"/><path d="M5.5 4.5l1.5 1.5-1 1c.6 1.3 1.6 2.3 3 3l1-1 1.5 1.5-1.2 1.2c-2.8-.6-5.3-3.1-6-6z" fill="#fff"/></svg>
    </li>
    <li><span>dpike@vfwayroutes.com</span>
      <svg class="icon" viewBox="0 0 16 16"><rect x="1" y="4" width="14" height="10" rx="1.5" fill="#fff"/><path d="M1.5 5l6.5 5 6.5-5" fill="none" stroke="#1170bb" stroke-width="1.3"/></svg>
    </li>
    <li><span>www.vfwayroutes.com</span>
      <svg class="icon" viewBox="0 0 16 16"><g fill="none" stroke="#fff" stroke-width="1.2"><circle cx="8" cy="8" r="6.5"/><ellipse cx="8" cy="8" rx="3" ry="6.5"/><path d="M1.5 8h13M2.5 5h11M2.5 11h11"/></g></svg>
    </li>
  </ul>
</section>

</body>
</html>
```